Business Card Design needed for start up company Halvora

In need of a new business card designed for a start up company based in Sydney, Halvora is a new start up innovative Company, our mission it to make property accessible for everyday Australian and to become the leading Real Estate platform in Australia. We want it to be fresh and clean.

Industry/Entity Type

Financial

Contact Information for Business Card

Section for Name
Section for Title

HALVORA - The Strength of Pooling
Mobile:
Direct:

Font styles to use
Sans Serif

Colors
33a6d7
0692cd
0255a3
ffffff

Requirements
Must have
• Logo, all business card details

```html
<!DOCTYPE html>
<html lang="en">
<head>
<meta charset="utf-8">
<title>Halvora Business Card</title>
<link href="https://fonts.googleapis.com/css2?family=Montserrat:wght@400;600;800&display=swap" rel="stylesheet">
<style>
  :root{
    --sky:#33a6d7;
    --azure:#0692cd;
    --navy:#0255a3;
    --deep-navy:#183f85;
    --white:#ffffff;
    --paper:#f1f2f4;
    --stage:#e4e6ea;
  }
  *{margin:0;padding:0;box-sizing:border-box}
  html,body{width:1200px;height:911px;overflow:hidden}
  body{
    background:var(--stage);
    font-family:"Montserrat",sans-serif;
    display:flex;flex-direction:column;align-items:center;justify-content:center;gap:56px;
  }
  .card{
    position:relative;width:560px;height:320px;border-radius:24px;overflow:hidden;
    box-shadow:0 10px 24px rgba(0,0,0,.18);
  }
  .card-front{background:var(--paper)}
  .front-swoosh{position:absolute;inset:0}
  .brand{position:absolute;display:flex;align-items:center;gap:10px}
  .brand-dot{border-radius:50%;flex:none}
  .brand-name{font-weight:800;letter-spacing:.5px;line-height:1;white-space:nowrap}
  .card-front .brand{left:34px;top:136px}
  .card-front .brand-dot{width:40px;height:40px;background:var(--azure)}
  .card-front .brand-name{font-size:32px;color:var(--navy)}
  .contact{
    position:absolute;left:345px;top:40px;color:var(--white);font-size:12px;line-height:1.45;
  }
  .contact-name{color:var(--sky);font-weight:800;font-size:17px;letter-spacing:.5px}
  .contact-title{font-size:14px;margin-bottom:14px}
  .contact-address{margin-bottom:14px}
  .contact-line{display:flex;align-items:center;gap:8px}
  .contact-icon{width:11px;height:11px;flex:none}
  .card-back{background:var(--sky)}
  .card-back .brand{left:110px;top:108px}
  .card-back .brand-dot{width:70px;height:70px;background:var(--white)}
  .card-back .brand-name{font-size:58px;color:var(--white)}
  .tagline{
    position:absolute;left:110px;top:212px;color:var(--white);font-size:14px;letter-spacing:.3px;
  }
</style>
</head>
<body>

<section class="card card-front" aria-label="Business card front">
  <svg class="front-swoosh" width="560" height="320" viewBox="0 0 560 320" aria-hidden="true">
    <path d="M250 0 H560 V320 H330 C330 180 300 70 250 0 Z" fill="var(--deep-navy)"/>
    <path d="M238 0 C292 72 322 170 322 320" fill="none" stroke="var(--navy)" stroke-width="4"/>
    <path d="M262 0 C310 70 336 170 338 320" fill="none" stroke="var(--sky)" stroke-width="1.5" opacity=".8"/>
  </svg>

  <div class="brand">
    <span class="brand-dot"></span>
    <span class="brand-name">HALVORA</span>
  </div>

  <div class="contact">
    <p class="contact-name">DANIEL REYES</p>
    <p class="contact-title">CEO/FOUNDER</p>
    <p class="contact-address">42 Harbour Row<br>Sydney, NSW 2000</p>
    <p class="contact-line">
      <svg class="contact-icon" viewBox="0 0 12 12" aria-hidden="true"><path d="M2 1h3l1 3-2 1a7 7 0 0 0 3 3l1-2 3 1v3c-6 0-9-3-9-9z" fill="var(--sky)"/></svg>
      0412 305 718
    </p>
    <p class="contact-line">
      <svg class="contact-icon" viewBox="0 0 12 12" aria-hidden="true"><rect x="1" y="1" width="10" height="10" rx="1.5" fill="none" stroke="var(--white)" stroke-width="1.4"/></svg>
      02 9174 6620
    </p>
    <p class="contact-line">
      <svg class="contact-icon" viewBox="0 0 12 12" aria-hidden="true"><rect x="1" y="2.5" width="10" height="7" rx="1" fill="var(--sky)"/><path d="M1 3l5 3.5L11 3" fill="none" stroke="var(--deep-navy)" stroke-width="1"/></svg>
      daniel@halvora.com
    </p>
    <p class="contact-line">
      <svg class="contact-icon" viewBox="0 0 12 12" aria-hidden="true"><circle cx="6" cy="6" r="5" fill="var(--sky)"/></svg>
      www.halvora.com
    </p>
  </div>
</section>

<section class="card card-back" aria-label="Business card back">
  <div class="brand">
    <span class="brand-dot"></span>
    <span class="brand-name">HALVORA</span>
  </div>
  <p class="tagline">The Strength of Pooling</p>
</section>

</body>
</html>
```